Hvac and insulation company needs good looking business card design

We are hvac and insulation company and looking for a new business cards that look to today standards designs

Target Market(s)

homeowners

Industry/Entity Type

Hvac

Contact Information for Business Card

Name: Walter Brinoku
Home comfort consultant
address: 4827 Dunmore St #215 Oakland, CA 94619
office: 888-316-2790
cell: 510-742-3185
Lic.# 584261
Email: walter@corvane-hvac.com
Web: corvane-hvac.com

Requirements
Must have
• clean and sleek look
Nice to have
• simple with a clean look
Should not have
• to busy business card

```html
<!DOCTYPE html>
<html lang="en">
<head>
<meta charset="utf-8">
<title>Corvane business cards</title>
<link href="https://fonts.googleapis.com/css2?family=Open+Sans:wght@400;600&family=Roboto:wght@400;500&display=swap" rel="stylesheet">
<style>
  :root {
    --backdrop: #2a2a2a;
    --card-light: #f4f4f4;
    --card-dark: #1b1b1b;
    --accent: #f7941d;
    --ink-light: #ffffff;
    --ink-muted: #555555;
    --divider: #6a6a6a;
  }
  * { margin: 0; padding: 0; box-sizing: border-box; }
  html, body { width: 1200px; height: 886px; overflow: hidden; }
  body {
    background: var(--backdrop);
    font-family: "Roboto", Arial, sans-serif;
    display: flex;
    flex-direction: column;
    align-items: center;
    justify-content: center;
    gap: 56px;
  }
  .card {
    width: 560px;
    height: 320px;
    border-radius: 18px;
    position: relative;
    overflow: hidden;
  }
  .card--front { background: var(--card-light); }
  .card--back { background: linear-gradient(135deg, #262626 0%, var(--card-dark) 60%, #141414 100%); }

  .brand {
    display: flex;
    align-items: center;
    gap: 14px;
  }
  .brand__dot {
    width: 34px; height: 34px;
    border-radius: 50%;
    background: var(--accent);
  }
  .brand__name {
    font-family: "Open Sans", Arial, sans-serif;
    font-weight: 600;
    color: var(--accent);
    letter-spacing: 0.5px;
  }

  .card--front .brand {
    position: absolute;
    left: 50%; top: 112px;
    transform: translateX(-50%);
  }
  .card--front .brand__name { font-size: 54px; line-height: 1; }
  .front__web {
    position: absolute;
    left: 0; right: 0; top: 228px;
    text-align: center;
    font-family: "Open Sans", Arial, sans-serif;
    font-size: 13px;
    letter-spacing: 7px;
    color: var(--ink-muted);
  }

  .card--back .brand {
    position: absolute;
    left: 34px; top: 186px;
  }
  .card--back .brand__dot { width: 28px; height: 28px; }
  .card--back .brand__name { font-size: 42px; line-height: 1; }

  .back__divider {
    position: absolute;
    left: 300px; top: 40px;
    width: 1px; height: 240px;
    background: linear-gradient(to bottom, transparent, var(--divider) 30%, var(--divider) 70%, transparent);
  }

  .contact {
    position: absolute;
    left: 322px; top: 54px;
    right: 20px;
    color: var(--ink-light);
  }
  .contact__name {
    font-size: 19px;
    font-weight: 500;
    color: var(--accent);
    text-transform: uppercase;
    letter-spacing: 0.3px;
  }
  .contact__role {
    font-size: 13px;
    font-weight: 500;
    text-transform: uppercase;
    margin-bottom: 14px;
  }
  .contact__address {
    font-size: 12.5px;
    line-height: 1.4;
    margin-bottom: 12px;
  }
  .contact__list { list-style: none; }
  .contact__item {
    display: flex;
    align-items: center;
    gap: 8px;
    font-size: 12.5px;
    line-height: 1.55;
  }
  .contact__icon { width: 12px; height: 12px; flex: none; }
</style>
</head>
<body>

<section class="card card--front">
  <div class="brand">
    <span class="brand__dot"></span>
    <span class="brand__name">corvane</span>
  </div>
  <p class="front__web">www.corvane-hvac.com</p>
</section>

<section class="card card--back">
  <div class="brand">
    <span class="brand__dot"></span>
    <span class="brand__name">corvane</span>
  </div>

  <div class="back__divider"></div>

  <div class="contact">
    <p class="contact__name">Walter Brinoku</p>
    <p class="contact__role">Home Comfort Consultant</p>
    <p class="contact__address">4827 Dunmore St #215<br>Oakland, CA 94619</p>
    <ul class="contact__list">
      <li class="contact__item">
        <svg class="contact__icon" viewBox="0 0 12 12"><path d="M2.5 1l2 2.4-1.1 1.2c.7 1.5 1.8 2.6 3.1 3.3l1.2-1.1L10.5 8.8 9.3 11C5 10.6 1.4 7 1 2.7z" fill="#f7941d"/></svg>
        <span>888-316-2790</span>
      </li>
      <li class="contact__item">
        <svg class="contact__icon" viewBox="0 0 12 12"><rect x="3" y="0.5" width="6" height="11" rx="1" fill="none" stroke="#f7941d" stroke-width="1.3"/><circle cx="6" cy="9.4" r="0.8" fill="#f7941d"/></svg>
        <span>510-742-3185</span>
      </li>
      <li class="contact__item">
        <svg class="contact__icon" viewBox="0 0 12 12"><rect x="1" y="2" width="10" height="8" rx="1" fill="#f7941d"/><rect x="2.5" y="4" width="7" height="1" fill="#1b1b1b"/><rect x="2.5" y="6.5" width="4.5" height="1" fill="#1b1b1b"/></svg>
        <span>Lic.# 584261</span>
      </li>
      <li class="contact__item">
        <svg class="contact__icon" viewBox="0 0 12 12"><rect x="0.5" y="2" width="11" height="8" rx="1" fill="#f7941d"/><path d="M1 2.6l5 3.8 5-3.8" fill="none" stroke="#1b1b1b" stroke-width="1"/></svg>
        <span>walter@corvane-hvac.com</span>
      </li>
      <li class="contact__item">
        <svg class="contact__icon" viewBox="0 0 12 12"><circle cx="6" cy="6" r="5.2" fill="#f7941d"/><path d="M0.8 6h10.4M6 0.8c-2.2 2.8-2.2 7.6 0 10.4M6 0.8c2.2 2.8 2.2 7.6 0 10.4" fill="none" stroke="#1b1b1b" stroke-width="0.8"/></svg>
        <span>corvane-hvac.com</span>
      </li>
    </ul>
  </div>
</section>

</body>
</html>
```